Brightfen Business Card Redesign & Logo Update

We need to update our business cards to something more modern and fresh. Brightfen can provide the current color schemes and old design examples, but welcome creativity in helping us with this redesign. PLEASE NOTE that we no longer utilize the "tree" and/or "leaf" imagery in our branding. If able would apprecaite an update on the quality of our "words only" logo in Ai. / PNG formats too.

Target Market(s)

Investors, landowners, corporate partners, contractors

Industry/Entity Type

Environmental Restoration & Conservation

Contact Information for Business Card

Logo, persons name, title, mailing address, phone and email, website url

Font styles to use
Other font styles liked:
• Merriweather

Requirements
Nice to have
• Logo, persons name, title, mailing address, phone and email, website url, but open to ideams
Should not have
• No all back backgrounds

```html
<!DOCTYPE html>
<html lang="en">
<head>
<meta charset="utf-8">
<title>Brightfen Business Card</title>
<link rel="stylesheet" href="https://fonts.googleapis.com/css2?family=Montserrat:wght@400;500;700;800&display=swap">
<style>
  :root {
    --backdrop: #e4e4e4;
    --card: #ffffff;
    --orange: #ec7f26;
    --green: #137d3f;
    --ink: #111111;
  }
  * { margin: 0; padding: 0; box-sizing: border-box; }
  html, body {
    width: 1160px;
    height: 1200px;
    overflow: hidden;
    background: var(--backdrop);
    font-family: "Montserrat", Arial, sans-serif;
    color: var(--ink);
  }
  .card {
    position: absolute;
    left: 199px;
    width: 777px;
    height: 442px;
    background: var(--card);
    border-radius: 26px;
  }
  .card--front { top: 105px; }
  .card--back { top: 634px; }

  .holder { position: absolute; left: 35px; top: 86px; }
  .holder__name {
    font-size: 24px;
    font-weight: 700;
    letter-spacing: 0.2px;
    line-height: 1;
  }
  .holder__first { color: var(--green); }
  .holder__last { color: var(--orange); }
  .holder__title {
    margin-top: 10px;
    font-size: 19px;
    font-weight: 500;
    line-height: 1;
  }

  .wordmark {
    position: absolute;
    font-weight: 800;
    color: var(--orange);
    line-height: 1;
    letter-spacing: 1px;
  }
  .wordmark--small { right: 39px; top: 80px; font-size: 50px; }
  .wordmark--large {
    left: 0; right: 0; top: 168px;
    text-align: center;
    font-size: 80px;
  }

  .contacts {
    position: absolute;
    left: 35px;
    top: 272px;
    list-style: none;
  }
  .contacts__item {
    display: flex;
    align-items: center;
    height: 34px;
    font-size: 22px;
    font-weight: 500;
  }
  .contacts__icon {
    width: 27px;
    height: 27px;
    margin-right: 13px;
    flex: none;
  }

  .address {
    position: absolute;
    right: 39px;
    top: 318px;
    font-style: normal;
    font-size: 20px;
    font-weight: 500;
    line-height: 28px;
    text-align: left;
  }
</style>
</head>
<body>
  <section class="card card--front">
    <div class="holder">
      <p class="holder__name"><span class="holder__first">DANA</span> <span class="holder__last">HOLLOWAY</span></p>
      <p class="holder__title">Managing Director</p>
    </div>

    <p class="wordmark wordmark--small">BRIGHTFEN</p>

    <ul class="contacts">
      <li class="contacts__item">
        <svg class="contacts__icon" viewBox="0 0 28 28" aria-hidden="true">
          <circle cx="14" cy="14" r="14" fill="var(--orange)"/>
          <path d="M7 11c0-2 3-3 7-3s7 1 7 3v1.5h-3.5V11h-7v1.5H7z" fill="#fff"/>
          <rect x="9" y="13" width="10" height="7" rx="1.5" fill="#fff"/>
        </svg>
        555-014-2273
      </li>
      <li class="contacts__item">
        <svg class="contacts__icon" viewBox="0 0 28 28" aria-hidden="true">
          <circle cx="14" cy="14" r="14" fill="var(--orange)"/>
          <rect x="7" y="9" width="14" height="10" rx="1" fill="none" stroke="#fff" stroke-width="1.8"/>
          <path d="M7.5 9.5 14 15l6.5-5.5" fill="none" stroke="#fff" stroke-width="1.8"/>
        </svg>
        info@brightfen.com
      </li>
      <li class="contacts__item">
        <svg class="contacts__icon" viewBox="0 0 28 28" aria-hidden="true">
          <circle cx="14" cy="14" r="14" fill="var(--orange)"/>
          <circle cx="14" cy="14" r="7.5" fill="none" stroke="#fff" stroke-width="1.8"/>
          <path d="M6.5 14h15M14 6.5c-3 3-3 12 0 15M14 6.5c3 3 3 12 0 15" fill="none" stroke="#fff" stroke-width="1.4"/>
        </svg>
        www.brightfen.com
      </li>
    </ul>

    <address class="address">
      42-07 Laurel Ave 18<br>
      Fairbrook, NY 11402
    </address>
  </section>

  <section class="card card--back">
    <p class="wordmark wordmark--large">BRIGHTFEN</p>
  </section>
</body>
</html>
```